Wellpath Ledgers New Website

Please review the attached Design Brief with additional details. Thank you!

The goal is to create a website that effectively communicates the benefits of WellPath Ledgers to eye care professionals. The website should streamline the process of understanding and utilizing WellPath Ledgers' services, emphasizing improved patient outcomes, increased referrals, and enhanced patient engagement.

Target Market(s)

Eyecare Professionals

Number of Pages Required

4 page

```html
<!DOCTYPE html>
<html lang="en">
<head>
<meta charset="utf-8">
<title>Wellpath Ledgers – Services</title>
<link href="https://fonts.googleapis.com/css2?family=Open+Sans:wght@400;600;700&family=Lato:wght@400;700&display=swap" rel="stylesheet">
<style>
:root{
  --navy:#0d4a73;
  --ink:#3f4347;
  --body:#5d6166;
  --orange:#f7a23b;
  --ring:#1f6fbf;
  --pale:#f3f8fc;
  --bubble:#e6eef6;
  --footer:#1a1323;
  --footer-chip:#2c2140;
  --topbar:#1d3a5e;
  --brand:#1f4fc7;
}
*{margin:0;padding:0;box-sizing:border-box}
html,body{width:1200px;height:2200px;overflow:hidden;background:#fff}
body{font-family:"Lato",sans-serif;color:var(--body)}
.canvas{position:relative;width:1200px;height:2200px;overflow:hidden}
.abs{position:absolute}

/* header */
.topbar{left:0;top:0;width:1200px;height:47px;background:linear-gradient(90deg,#2a4d74,var(--topbar) 60%,#27466c)}
.topbar-text{top:21px;font-family:"Open Sans",sans-serif;font-size:10px;color:#fff;font-weight:600}
.social-dot{top:23px;width:8px;height:8px;border-radius:2px;background:#fff}
.quote{left:845px;top:20px;width:111px;height:14px;text-align:center;font-family:"Open Sans",sans-serif;font-size:10px;font-weight:600;color:#fff;border-bottom:5px solid #4f8a7b;line-height:10px}
.nav-band{left:0;top:47px;width:1200px;height:44px;background:#fff}
.brand-tab{left:0;top:0}
.brand{left:78px;top:32px;font-family:"Open Sans",sans-serif;font-weight:700;font-size:20px;color:var(--brand);display:flex;align-items:center;gap:7px}
.brand-dot{width:12px;height:12px;border-radius:50%;background:var(--orange)}
.tagline{left:82px;top:70px;font-family:"Open Sans",sans-serif;font-size:11px;color:#222}
.nav a{position:absolute;top:61px;font-family:"Open Sans",sans-serif;font-size:12px;color:#6b6f74;text-decoration:none}
.nav a.home{color:#2a76b5}
.nav a.active{color:#1a5b8e;font-weight:700}

/* hero */
.hero{left:0;top:91px;width:1200px;height:258px;background:linear-gradient(100deg,#2c4a78 0%,#3a5d8e 45%,#2b4c7c 75%,#345a8c 100%)}
.hero-kicker{left:107px;top:187px;font-family:"Open Sans",sans-serif;font-size:20px;color:#fff}
.hero-title{left:106px;top:216px;font-family:"Open Sans",sans-serif;font-weight:700;font-size:52px;color:#fff}
.hero-rule{left:0;top:348px;width:1200px;height:4px;background:var(--orange)}

/* service blocks */
.band{left:0;width:1200px;overflow:hidden}
.band.pale{background:var(--pale)}
.svc-title{font-family:"Open Sans",sans-serif;font-weight:700;font-size:36px;color:var(--ink);white-space:nowrap}
.svc-title span{color:var(--navy)}
.dash{width:36px;height:2px;background:var(--orange)}
.svc-copy{width:410px;font-size:13px;line-height:25px;color:var(--body)}
.btn{width:116px;height:31px;border:2px solid var(--navy);border-radius:16px;text-align:center;line-height:27px;font-family:"Open Sans",sans-serif;font-weight:600;font-size:11px;color:var(--navy)}
.photo{width:538px;height:538px;border-radius:50%;border:4px solid var(--ring)}
.bubble{width:116px;height:116px;border-radius:50%;background:var(--bubble);display:flex;align-items:center;justify-content:center}

/* footer */
.footer{left:0;top:1700px;width:1200px;height:500px;background:var(--footer)}
.wave{left:0;top:1620px}
.f-brand{left:126px;top:1764px;font-family:"Open Sans",sans-serif;font-weight:700;font-size:30px;color:var(--brand);display:flex;align-items:center;gap:9px}
.f-brand i{width:16px;height:16px;border-radius:50%;background:var(--orange);display:block}
.f-text{font-size:13px;line-height:22px;color:#c9c4d3}
.chip{top:1915px;width:31px;height:31px;border-radius:4px;background:var(--footer-chip)}
.chip.on{background:var(--orange)}
.f-head{top:1773px;font-weight:700;font-size:16px;color:#fff}
.f-links{top:1818px;list-style:none;font-size:13px;line-height:26px;color:#c9c4d3}
.sub-form{left:827px;top:1873px;width:243px;height:47px;display:flex}
.sub-form .field{flex:1;background:#fff;font-family:"Open Sans",sans-serif;font-size:12px;color:#777;padding:0 24px;line-height:47px}
.sub-form .go{width:50px;background:var(--orange);display:flex;align-items:center;justify-content:center}
.info-icon{top:2027px;width:48px;height:48px;border-radius:50%;background:var(--footer-chip);display:flex;align-items:center;justify-content:center}
.info-icon.on{background:var(--orange)}
.info-title{top:2030px;font-weight:700;font-size:16px;color:#fff}
.info-sub{top:2054px;font-size:13px;color:#c9c4d3}
.f-rule{left:126px;top:2142px;width:946px;height:1px;background:#3a2f4a}
.f-bottom{left:0;top:2162px;width:1200px;text-align:center;font-family:"Open Sans",sans-serif;font-size:13px;color:#fff}
</style>
</head>
<body>
<div class="canvas">

  <!-- header -->
  <div class="abs topbar"></div>
  <svg class="abs brand-tab" width="440" height="92" viewBox="0 0 440 92" aria-hidden="true">
    <path d="M0 23 H392 C410 23 418 47 440 47 V92 H0 Z" fill="#fff"/>
  </svg>
  <div class="abs nav-band"></div>
  <div class="abs brand"><span class="brand-dot"></span>Wellpath Ledgers</div>
  <div class="abs tagline">Empowering Healthcare</div>

  <svg class="abs" style="left:468px;top:22px" width="8" height="11" viewBox="0 0 8 11" aria-hidden="true"><path d="M4 0a4 4 0 0 1 4 4c0 3-4 7-4 7S0 7 0 4a4 4 0 0 1 4-4z" fill="#fff"/><circle cx="4" cy="4" r="1.5" fill="#1d3a5e"/></svg>
  <div class="abs topbar-text" style="left:483px">48 Harbor Lane, Springvale, 00012</div>
  <div class="abs topbar-text" style="left:706px">Follow Us:</div>
  <span class="abs social-dot" style="left:767px"></span>
  <span class="abs social-dot" style="left:781px"></span>
  <span class="abs social-dot" style="left:797px"></span>
  <div class="abs quote">GET QUOTATION</div>

  <nav class="nav">
    <a class="home" style="left:448px">Home</a>
    <a style="left:542px">About Us</a>
    <a style="left:629px">Conditions</a>
    <a class="active" style="left:723px">Services</a>
    <a style="left:829px">Gallery</a>
    <a style="left:910px">Team</a>
    <a style="left:992px">Contact Us</a>
  </nav>

  <!-- hero -->
  <div class="abs hero" role="img" aria-label="Photo of clinicians working together at computer screens, tinted blue"></div>
  <div class="abs hero-kicker">OUR SERVICES</div>
  <div class="abs hero-title">Services We Offer</div>
  <div class="abs hero-rule"></div>

  <!-- health analytics -->
  <section class="abs band" style="top:352px;height:423px">
    <div class="abs photo" style="left:747px;top:63px;background:linear-gradient(135deg,#dfe4e8 0%,#a9c4da 45%,#6f9cc4 75%,#4f6b84 100%)" role="img" aria-label="Photo of a masked healthcare worker typing at a computer in a records room"></div>
    <div class="abs bubble" style="left:721px;top:105px">
      <svg width="52" height="52" viewBox="0 0 52 52" fill="none" stroke="#f7a23b" stroke-width="2.4" aria-hidden="true">
        <circle cx="22" cy="22" r="17"/><path d="M5 22h34M22 5c-6 6-6 28 0 34M22 5c6 6 6 28 0 34"/>
        <circle cx="36" cy="36" r="9" fill="#e6eef6"/><circle cx="36" cy="36" r="3.5"/>
      </svg>
    </div>
    <h2 class="abs svc-title" style="left:147px;top:80px">Health <span>Analytics</span></h2>
    <div class="abs dash" style="left:145px;top:153px"></div>
    <p class="abs svc-copy" style="left:194px;top:144px">Lorem ipsum dolor sit amet, consectetur adipiscing elit, sed do eiusmod tempor incididunt ut labore et dolore magna aliqua. Ut enim ad minim veniam, quis nostrud exercitation ullamco laboris nisi ut aliquip ex ea commodo consequat. Duis aute irure dolor in reprehenderit in voluptate velit esse cillum dolore eu fugiat nulla paria</p>
    <div class="abs btn" style="left:195px;top:298px">CONTACT US</div>
  </section>

  <!-- outcome monitoring -->
  <section class="abs band pale" style="top:775px;height:419px">
    <div class="abs photo" style="left:-85px;top:62px;background:linear-gradient(120deg,#efe9df 0%,#d9cdb8 40%,#b9a583 75%,#8f8a5e 100%)" role="img" aria-label="Photo of a doctor in a white coat writing notes at a desk"></div>
    <div class="abs bubble" style="left:362px;top:99px">
      <svg width="44" height="44" viewBox="0 0 44 44" fill="none" stroke="#f7a23b" stroke-width="2.4" aria-hidden="true">
        <path d="M22 3l4 5 6-2 1 6 6 2-2 6 4 4-4 4 2 6-6 2-1 6-6-2-4 5-4-5-6 2-1-6-6-2 2-6-4-4 4-4-2-6 6-2 1-6 6 2z"/>
        <circle cx="22" cy="22" r="7"/>
      </svg>
    </div>
    <h2 class="abs svc-title" style="left:602px;top:84px">Outcome <span>Monitoring</span></h2>
    <div class="abs dash" style="left:600px;top:158px"></div>
    <p class="abs svc-copy" style="left:649px;top:149px">Lorem ipsum dolor sit amet, consectetur adipiscing elit, sed do eiusmod tempor incididunt ut labore et dolore magna aliqua. Ut enim ad minim veniam, quis nostrud exercitation ullamco laboris nisi ut aliquip ex ea commodo consequat. Duis aute irure dolor in reprehenderit in voluptate velit esse cillum dolore eu fugiat nulla paria</p>
    <div class="abs btn" style="left:650px;top:303px">CONTACT US</div>
  </section>

  <!-- engagement tools -->
  <section class="abs band" style="top:1194px;height:526px">
    <div class="abs photo" style="left:747px;top:61px;background:linear-gradient(140deg,#e4dff0 0%,#a9a6cf 35%,#5e6a98 65%,#2c3752 100%)" role="img" aria-label="Photo of a clinician's hands typing on a laptop beside a stethoscope and notebook"></div>
    <div class="abs bubble" style="left:721px;top:103px">
      <svg width="48" height="44" viewBox="0 0 48 44" fill="none" stroke="#f7a23b" stroke-width="2.4" aria-hidden="true">
        <circle cx="24" cy="13" r="7"/><path d="M12 40v-4a12 12 0 0 1 24 0v4z"/>
        <circle cx="9" cy="14" r="5"/><path d="M2 32a8 8 0 0 1 9-8"/>
        <circle cx="39" cy="14" r="5"/><path d="M46 32a8 8 0 0 0-9-8"/>
      </svg>
    </div>
    <h2 class="abs svc-title" style="left:147px;top:78px">Engagement <span>Tools</span></h2>
    <div class="abs dash" style="left:145px;top:151px"></div>
    <p class="abs svc-copy" style="left:194px;top:142px">Lorem ipsum dolor sit amet, consectetur adipiscing elit, sed do eiusmod tempor incididunt ut labore et dolore magna aliqua. Ut enim ad minim veniam, quis nostrud exercitation ullamco laboris nisi ut aliquip ex ea commodo consequat. Duis aute irure dolor in reprehenderit in voluptate velit esse cillum dolore eu fugiat nulla paria</p>
    <div class="abs btn" style="left:195px;top:297px">CONTACT US</div>
  </section>

  <!-- footer -->
  <svg class="abs wave" width="1200" height="100" viewBox="0 0 1200 100" aria-hidden="true">
    <path d="M0 50 C150 25 300 8 420 14 C600 22 760 70 900 76 C1020 80 1120 70 1200 62 V100 H0 Z" fill="#f7a23b"/>
    <path d="M0 92 C100 60 220 44 330 44 C520 46 700 86 860 88 C1000 90 1110 76 1200 68 V100 H0 Z" fill="#1a1323"/>
  </svg>
  <footer class="abs footer"></footer>

  <div class="abs f-brand"><i></i>Wellpath Ledgers</div>
  <p class="abs f-text" style="left:126px;top:1843px;width:300px">Lorem ipsum dolor sit amet, consectetur adipiscing elit, sed do eiusmod tempor incididunt ut</p>
  <span class="abs chip on" style="left:126px"></span>
  <span class="abs chip" style="left:164px"></span>
  <span class="abs chip" style="left:202px"></span>
  <span class="abs chip" style="left:240px"></span>

  <h3 class="abs f-head" style="left:489px">Quick Links</h3>
  <ul class="abs f-links" style="left:490px">
    <li>Home</li><li>Services</li><li>About Us</li><li>Contact</li><li>Blog</li><li>Testimonials</li>
  </ul>
  <ul class="abs f-links" style="left:625px">
    <li>Cookies Policy</li><li>Terms of Use</li><li>Careers</li><li>Our Team</li><li>More</li>
  </ul>

  <h3 class="abs f-head" style="left:827px">Newsletters</h3>
  <p class="abs f-text" style="left:827px;top:1812px;width:250px">Lorem ipsum dolor sit amet, consectetur adipiscing elit, sed do eiusmod tempor</p>
  <div class="abs sub-form">
    <div class="field">Enter Email Address</div>
    <div class="go"><svg width="14" height="18" viewBox="0 0 14 18" aria-hidden="true"><path d="M3 2l8 7-8 7" fill="none" stroke="#fff" stroke-width="3"/></svg></div>
  </div>

  <div class="abs info-icon" style="left:125px"><svg width="14" height="20" viewBox="0 0 14 20" aria-hidden="true"><path d="M7 0a7 7 0 0 1 7 7c0 5-7 13-7 13S0 12 0 7a7 7 0 0 1 7-7z" fill="#5a4a78"/><circle cx="7" cy="7" r="2.5" fill="#2c2140"/></svg></div>
  <div class="abs info-title" style="left:190px">Address</div>
  <div class="abs info-sub" style="left:190px">48 Harbor Lane</div>

  <div class="abs info-icon on" style="left:365px"><svg width="22" height="16" viewBox="0 0 22 16" aria-hidden="true"><rect x="1" y="1" width="20" height="14" rx="1" fill="none" stroke="#fff" stroke-width="2"/><path d="M1 1l10 8 10-8" fill="none" stroke="#fff" stroke-width="2"/></svg></div>
  <div class="abs info-title" style="left:429px">Email Us</div>
  <div class="abs info-sub" style="left:429px">support@wellpathmail.net</div>

  <div class="abs info-icon" style="left:632px"><svg width="18" height="18" viewBox="0 0 18 18" aria-hidden="true"><path d="M4 1l3 4-2 2c1 2 3 4 5 5l2-2 4 3-2 3C8 16 2 10 1 4z" fill="#5a4a78"/></svg></div>
  <div class="abs info-title" style="left:696px">Contact Us</div>
  <div class="abs info-sub" style="left:696px">+010 (2345) 678 90</div>

  <div class="abs info-icon" style="left:859px"><svg width="22" height="22" viewBox="0 0 22 22" aria-hidden="true"><circle cx="11" cy="11" r="9.5" fill="none" stroke="#5a4a78" stroke-width="2"/><path d="M11 5v6h5" fill="none" stroke="#5a4a78" stroke-width="2"/></svg></div>
  <div class="abs info-title" style="left:923px">Opening Hour</div>
  <div class="abs info-sub" style="left:923px">Mon - Friday 10 am - 8pm</div>

  <div class="abs f-rule"></div>
  <div class="abs f-bottom">WELLPATH LEDGERS</div>
</div>
</body>
</html>
```